Web Design for an Innovative Life Science Marketplace

IMPORTANT:
The software is called CS-Cart. It has capabilities and limitations with design features in the software. There is a certain framework that needs to be followed. It is PHP and Linux. It may require add-ons for your design, so please be specific with what is required. It’s preferred the designer has CS-Cart knowledge/experience.

Key Requirements
1. I’d like the design to include an implemented/recommended CS-Cart theme that is consistent with our branding (see the marketing collateral and logo).
2. I then need the additional design changes to that theme to create the below web pages.
3. All designs should be consistent with our branding. All pictures should either be computer generated (clip art-like) or pictures of happy patients. What is a happy patient? Close up photo of someone healthy, happy, and experiencing/enjoying life. Not someone in a hospital or getting care. Please see examples already on the site.

Please see the attached Web Design details in the word document. That document is important to complete the design.

```html
<!DOCTYPE html>
<html lang="en">
<head>
<meta charset="utf-8">
<title>Vialink – About</title>
<link href="https://fonts.googleapis.com/css2?family=Roboto:wght@400;500;700;900&family=Roboto+Condensed:wght@400;700&display=swap" rel="stylesheet">
<style>
:root{
  --teal:#1b9085;
  --teal-dark:#157a70;
  --teal-foot:#2a9d90;
  --lime:#8dc63f;
  --lime-text:#7fbf2a;
  --nav-active:#c8e34a;
  --ink:#333;
  --body:#6b6b6b;
  --dark:#2a2a2a;
  --white:#fff;
}
*{box-sizing:border-box;margin:0;padding:0}
html,body{width:949px;height:1200px;overflow:hidden;background:#fff}
body{position:relative;font-family:'Roboto',sans-serif;color:var(--ink)}
.abs{position:absolute}

/* top bar */
.topbar{top:0;left:0;width:949px;height:22px;border-bottom:1px solid #eee}
.topbar .item{top:6px;font-size:7.5px;color:#555;text-transform:uppercase;display:flex;align-items:center;gap:5px;white-space:nowrap}
.topbar .item svg{width:9px;height:9px}
.topbar .item .num{font-size:8.5px}
.btn-pill{top:2px;height:19px;border-radius:10px;color:#fff;font-size:7.5px;font-weight:700;display:flex;align-items:center;justify-content:center;gap:3px}
.btn-login{left:703px;width:50px;background:var(--teal)}
.btn-register{left:756px;width:64px;background:var(--lime)}

/* header */
.brand{left:127px;top:36px;display:flex;align-items:center;gap:6px}
.brand .mark{width:22px;height:22px;border-radius:50%;background:var(--teal)}
.brand .name{font-size:20px;font-weight:900;color:var(--teal);letter-spacing:.5px}
.cart-icon{left:502px;top:35px;width:40px;height:36px;background:var(--lime);display:flex;align-items:center;justify-content:center}
.cart-text{left:549px;top:36px}
.cart-text .title{font-family:'Roboto Condensed',sans-serif;font-size:13px;color:#555;font-weight:400}
.cart-text .count{font-size:7.5px;color:#777;font-weight:700;display:flex;align-items:center;gap:3px;margin-top:-1px}
.cart-text .count b{font-size:16px;color:var(--lime)}
.search{left:665px;top:39px;width:156px;height:27px;border:1px solid #eee;border-radius:14px;background:#fafafa;font-size:8px;color:#999;padding-left:13px;display:flex;align-items:center}
.search .go{position:absolute;right:4px;top:4px;width:19px;height:19px;border-radius:50%;background:var(--lime);display:flex;align-items:center;justify-content:center}

/* nav */
.mainnav{top:84px;left:0;width:949px;height:31px;background:linear-gradient(#1fa093,var(--teal-dark))}
.mainnav ul{list-style:none;position:absolute;left:127px;top:0;display:flex;height:31px}
.mainnav li{font-size:8.5px;font-weight:700;color:#fff;line-height:31px;padding:0 18px;border-right:1px solid rgba(255,255,255,.15)}
.mainnav li:first-child{padding-left:0;color:var(--nav-active)}
.mainnav li:last-child{border:none}

/* hero */
.hero{top:115px;left:0;width:949px;height:184px;background:linear-gradient(90deg,#7f9a3a 0%,#a7b861 30%,#8e9a4f 55%,#c08a5a 72%,#9c8047 100%)}
.page-title{left:127px;top:172px;display:flex;align-items:flex-end;gap:4px;color:#fff;font-weight:700}
.page-title .rule{width:21px;height:1.5px;background:#fff;margin-bottom:16px}
.page-title .rule.long{width:61px;margin-left:2px}
.page-title .cap{font-size:72px;line-height:.8}
.page-title .rest{font-size:31px;line-height:1;margin-left:-2px}

/* about */
.frame-v{left:127px;top:359px;width:12px;height:258px;background:var(--teal)}
.frame-h{left:127px;top:606px;width:227px;height:11px;background:var(--teal)}
.about-photo{left:139px;top:346px;width:227px;height:260px;background:linear-gradient(135deg,#6b4a36,#c7a58a 45%,#8b7a67 75%,#5a4a3e)}
.about-head{left:394px;top:352px;display:flex;align-items:flex-end;font-weight:700;white-space:nowrap}
.about-head .cap{font-size:74px;line-height:.8;color:#3a3a3a}
.about-head .rest{font-size:30px;line-height:1;color:#3a3a3a;margin-left:-2px}
.about-head .brandword{font-size:30px;line-height:1;color:var(--lime-text);margin-left:5px}
.about-copy{left:394px;top:427px;width:428px;font-size:8.1px;line-height:14.2px;color:var(--body);text-align:justify}
.about-copy p{margin-bottom:11px}

/* contact band */
.band{top:661px;left:0;width:949px;height:116px;background:linear-gradient(90deg,#94c840,#87c23a 50%,#9ccd4a)}
.band .cell{top:30px;display:flex;align-items:center;gap:11px;color:#fff;white-space:nowrap}
.band .ring{width:56px;height:56px;border:2.5px solid #fff;border-radius:50%;display:flex;align-items:center;justify-content:center}
.band .big{font-size:13.5px;font-weight:700}
.band .small{font-size:8px;font-weight:700;text-transform:uppercase;margin-top:4px}

/* dark footer */
.dark{top:777px;left:0;width:949px;height:383px;background:var(--dark)}
.section-title{display:flex;align-items:flex-end;font-weight:700;color:#fff;white-space:nowrap}
.section-title .cap{color:var(--teal-foot);line-height:.8}
.connect{left:0;width:949px;top:814px;justify-content:center}
.connect .cap{font-size:46px}
.connect .rest{font-size:18px;line-height:1}
.socials{top:861px;left:426px;display:flex;gap:5px}
.socials span{width:29px;height:29px;border:1.5px solid #ddd;border-radius:3px}
.col-title{top:930px}
.col-title .cap{font-size:44px}
.col-title .rest{font-size:18px;line-height:1}
.col-rule{top:970px;width:18px;height:2px;background:#fff}
.email-field{left:127px;top:991px;width:193px;height:34px;border-radius:17px;background:#d6d6d6;font-size:8.5px;color:#888;padding-left:18px;display:flex;align-items:center}
.subscribe{left:132px;top:1030px;width:101px;height:24px;border-radius:12px;background:var(--teal-foot);color:#fff;font-size:10px;font-weight:700;display:flex;align-items:center;justify-content:center}
.tweets{left:367px;top:989px;width:193px;font-size:10px;line-height:14px;color:#ccc}
.tweets li{list-style:none;padding-bottom:8px;margin-bottom:7px;border-bottom:1px solid #3d3d3d}
.tweets li:last-child{border:none}
.tweets a{color:var(--teal-foot);text-decoration:underline}
.map{left:598px;top:992px;width:214px;height:117px;background:linear-gradient(135deg,#dfe3d8 0%,#d4dccd 55%,#a9c0e4 70%,#9db6df 100%)}

/* bottom bar */
.bottombar{top:1160px;left:0;width:949px;height:40px;background:var(--teal-foot)}
.bottombar ul{list-style:none;position:absolute;left:136px;top:0;display:flex;gap:26px;line-height:40px;font-size:7.8px;color:#fff}
.bottombar .copy{position:absolute;right:128px;top:0;line-height:40px;font-size:7.5px;color:#fff}
</style>
</head>
<body>

<div class="abs topbar">
  <div class="abs item" style="left:127px"><svg viewBox="0 0 10 10"><path d="M0 2l3-1 4 1 3-1v7l-3 1-4-1-3 1z" fill="#1b9085"/></svg>Adress : 48 Harbor Lane, NY</div>
  <div class="abs item" style="left:315px"><svg viewBox="0 0 10 10"><rect x="0" y="1" width="10" height="8" rx="1" fill="#1b9085"/><path d="M1 2l4 3 4-3" stroke="#fff" fill="none"/></svg>Email : hello@vialinkqc.com</div>
  <div class="abs item" style="left:487px"><svg viewBox="0 0 10 10"><path d="M2 0l2 2-1 2 3 3 2-1 2 2-2 2C4 10 0 6 0 2z" fill="#1b9085"/></svg>Call us : <span class="num">555-014-2290</span></div>
  <div class="abs item" style="left:625px"><svg viewBox="0 0 10 10"><circle cx="5" cy="3" r="2.5" fill="#1b9085"/><path d="M0 10c0-4 10-4 10 0z" fill="#1b9085"/></svg>My Account</div>
  <div class="abs btn-pill btn-login">&#128274; LOGIN</div>
  <div class="abs btn-pill btn-register">&#128274; REGISTER</div>
</div>

<div class="abs brand"><span class="mark"></span><span class="name">VIALINK</span></div>

<div class="abs cart-icon">
  <svg width="26" height="22" viewBox="0 0 26 22" fill="none" stroke="#fff" stroke-width="1.8"><path d="M1 2h4l3 12h13l3-9H7"/><circle cx="10" cy="19" r="2"/><circle cx="19" cy="19" r="2"/></svg>
</div>
<div class="abs cart-text">
  <div class="title">SHOPPING CART</div>
  <div class="count"><b>(0)</b>ITEM SELECTED</div>
</div>
<div class="abs search">Search Product ...
  <span class="go"><svg width="9" height="9" viewBox="0 0 10 10" fill="none" stroke="#fff" stroke-width="1.8"><circle cx="4" cy="4" r="3"/><path d="M6.5 6.5L9 9"/></svg></span>
</div>

<nav class="abs mainnav">
  <ul><li>HOME</li><li>ABOUT US</li><li>HOW IT WORKS</li><li>OUR PLATFORM</li><li>BENEFITS</li><li>CONTACT US</li></ul>
</nav>

<div class="abs hero" role="img" aria-label="Smiling young woman resting her chin on her hand in a sunny green meadow"></div>
<h1 class="abs page-title"><span class="rule"></span><span class="cap">A</span><span class="rest">BOUT</span><span class="rule long"></span></h1>

<div class="abs frame-v"></div>
<div class="abs frame-h"></div>
<div class="abs about-photo" role="img" aria-label="Happy woman with long brown hair holding a coffee cup"></div>

<h2 class="abs about-head"><span class="cap">A</span><span class="rest">BOUT</span><span class="brandword">VIALINK</span></h2>
<div class="abs about-copy">
  <p>We are a private and virtual B2B marketplace and consortium for life science manufacturers, researchers, and vendors to sell, purchase, and donate before and aftermarket materials and equipment as well as collaborate on non-financial ventures.</p>
  <p>We are in the developmental phase of our platform working with some of the most trusted and best industry partners. We are tentatively scheduled for an exclusive launch before the end of 2018.</p>
  <p>We aspire to transform the life science industry's paradigm of waste and material procurement to one that emphasizes stewardship, innovation, and robust collaboration while maintaining, and even exceeding, quality compliance/assurance (QMS 12, GPX 7, LSQA, QCB, etc). Patients deserve greater access and high-quality products, and our unique solution allows us to collectively delivery as an industry.</p>
</div>

<section class="abs band">
  <div class="abs cell" style="left:135px">
    <span class="ring"><svg width="24" height="24" viewBox="0 0 24 24"><path d="M5 2l5 5-2 3 6 6 3-2 5 5-3 3C10 22 2 14 2 5z" fill="#fff"/></svg></span>
    <div><div class="big">555-014-2290</div><div class="small">Call us for enquiry</div></div>
  </div>
  <div class="abs cell" style="left:369px">
    <span class="ring"><svg width="26" height="20" viewBox="0 0 26 20" fill="none" stroke="#fff" stroke-width="1.6"><rect x="1" y="1" width="24" height="18"/><path d="M1 1l12 10 12-10M1 19l9-8M25 19l-9-8"/></svg></span>
    <div><div class="big">hello@vialinkqc.com</div><div class="small">Drop us a line anytime!</div></div>
  </div>
  <div class="abs cell" style="left:627px">
    <span class="ring"><svg width="20" height="26" viewBox="0 0 20 26"><path d="M10 0a9 9 0 0 0-9 9c0 7 9 17 9 17s9-10 9-17a9 9 0 0 0-9-9z" fill="#fff"/><circle cx="10" cy="9" r="3.5" fill="#8dc63f"/></svg></span>
    <div><div class="big">48 Harbor Lane, NY</div><div class="small">Company address</div></div>
  </div>
</section>

<footer class="abs dark"></footer>
<h2 class="abs section-title connect"><span class="cap">C</span><span class="rest">ONNECT WITH US</span></h2>
<div class="abs socials"><span></span><span></span><span></span></div>

<h3 class="abs section-title col-title" style="left:127px"><span class="cap">N</span><span class="rest">EWSLETTER</span></h3>
<h3 class="abs section-title col-title" style="left:367px"><span class="cap">T</span><span class="rest">IMELINE</span></h3>
<h3 class="abs section-title col-title" style="left:597px"><span class="cap">L</span><span class="rest">OCATION</span></h3>
<div class="abs col-rule" style="left:127px"></div>
<div class="abs col-rule" style="left:368px"></div>
<div class="abs col-rule" style="left:598px"></div>

<div class="abs email-field">ENTER YOUR EMAIL ID</div>
<div class="abs subscribe">SUBSCRIBE</div>

<ul class="abs tweets">
  <li><a>@vial_qc:</a> Phasellus dapibus tellus at nibh lobortis, vitae placerat sapien tempor.</li>
  <li><a>@vial_qc:</a> Phasellus dapibus tellus at nibh lobortis, vitae placerat sapien tempor.</li>
  <li><a>@vial_qc:</a> Phasellus dapibus tellus at nibh lobortis, vitae placerat sapien tempor.</li>
</ul>

<div class="abs map" role="img" aria-label="Street map of the company location by the waterfront"></div>

<div class="abs bottombar">
  <ul><li>HOME</li><li>ABOUT US</li><li>HOW IT WORKS</li><li>OUR PLATFORM</li><li>BENEFITS</li><li>CONTACT US</li></ul>
  <div class="copy">© 2018 VIALINK . ALL RIGHTS RESERVED</div>
</div>

</body>
</html>
```